landscaping core flute signs

I need core flutes created with business name and a few extra dot points for putting on fences for job sites 120cm x 120cm approx.
I want our old ones information with the new L logo and colour palette

```html
<!DOCTYPE html>
<html lang="en">
<head>
<meta charset="utf-8">
<title>Grounded Form – Job Site Sign</title>
<link rel="stylesheet" href="https://fonts.googleapis.com/css2?family=Montserrat:wght@500;600;700&family=Cinzel:wght@400&display=swap">
<style>
  :root {
    --backdrop: #9a9a9a;
    --sign-white: #ffffff;
    --ink: #231f20;
    --ink-soft: #2b2b2b;
    --leaf-green: #5f8c58;
    --stripe-black: #111111;
  }
  * { box-sizing: border-box; margin: 0; padding: 0; }
  html, body {
    width: 1200px;
    height: 829px;
    overflow: hidden;
    background: var(--backdrop);
    font-family: "Montserrat", Arial, sans-serif;
  }
  .sign {
    position: absolute;
    left: 282px;
    top: 96px;
    width: 636px;
    height: 636px;
    background: var(--sign-white);
    overflow: hidden;
  }
  .brand-mark {
    position: absolute;
    left: 247px;
    top: 37px;
    width: 142px;
    height: 142px;
    border-radius: 50%;
    background: var(--leaf-green);
  }
  .brand-name {
    position: absolute;
    left: 0;
    width: 100%;
    top: 198px;
    text-align: center;
    font-weight: 600;
    font-size: 31px;
    letter-spacing: 1px;
    color: var(--ink);
    line-height: 1;
  }
  .tagline {
    position: absolute;
    left: 0;
    width: 100%;
    top: 241px;
    display: flex;
    justify-content: center;
    align-items: center;
    gap: 10px;
    font-family: "Cinzel", Georgia, serif;
    font-size: 11px;
    letter-spacing: 3px;
    color: var(--leaf-green);
    line-height: 14px;
  }
  .tagline .rule {
    width: 50px;
    height: 2px;
    background: var(--ink);
  }
  .services {
    position: absolute;
    left: 0;
    width: 100%;
    top: 309px;
    list-style: none;
    display: flex;
    flex-direction: column;
    align-items: center;
    gap: 18px;
  }
  .services li {
    display: flex;
    align-items: center;
    gap: 10px;
    font-weight: 500;
    font-size: 24px;
    color: var(--ink-soft);
    line-height: 32px;
  }
  .services .dot {
    width: 18px;
    height: 18px;
    border-radius: 50%;
    background: var(--leaf-green);
  }
  .phone {
    position: absolute;
    left: 0;
    width: 100%;
    top: 453px;
    text-align: center;
    font-weight: 700;
    font-size: 57px;
    color: var(--ink-soft);
    line-height: 1;
  }
  .email {
    position: absolute;
    left: 0;
    width: 100%;
    top: 527px;
    text-align: center;
    font-weight: 600;
    font-size: 27px;
    color: var(--ink-soft);
    line-height: 1;
  }
  .footer-wave {
    position: absolute;
    left: 0;
    bottom: 0;
    width: 636px;
    height: 76px;
  }
  .licence {
    position: absolute;
    right: 47px;
    bottom: 26px;
    font-weight: 700;
    font-size: 18px;
    line-height: 20px;
    color: var(--sign-white);
    letter-spacing: 0.5px;
  }
</style>
</head>
<body>
  <main class="sign">
    <div class="brand-mark" aria-hidden="true"></div>
    <h1 class="brand-name">GROUNDED FORM</h1>
    <p class="tagline"><span class="rule"></span>STRUCTURAL LANDSCAPING<span class="rule"></span></p>

    <ul class="services">
      <li><span class="dot"></span>Paving &amp; Concreting</li>
      <li><span class="dot"></span>Fencing &amp; Retaining</li>
      <li><span class="dot"></span>Design &amp; Construct</li>
    </ul>

    <p class="phone">0412 555 019</p>
    <p class="email">sam@groundedform.com</p>

    <svg class="footer-wave" viewBox="0 0 636 76" preserveAspectRatio="none" aria-hidden="true">
      <path fill="var(--leaf-green)" d="M0 52 C 200 54 420 10 636 16 L636 76 L0 76 Z"/>
      <path fill="var(--stripe-black)" d="M0 22 C 220 40 420 10 560 6 C 420 14 220 54 0 38 Z"/>
    </svg>
    <p class="licence">QBSA:&nbsp; 1042318</p>
  </main>
</body>
</html>
```